Business card for Eyelash extension salon in Beverly Hills,California USA

We need new business card for our salon in Beverly Hills. The salon name is 'Lashvera' . We would like to have...Business name: Lashvera Name of person: will provide later Address 4720 N.Alder Crest Ave Larkspur Heights , CA 90299 Phone: will provide later (Text only) Web: www.lashverastudio.example Snapgrid icon, Circlebook icon follow us for seasonal campaign and news @lashverastudiolounge Design should look elegant, high-end, clean, simple, cohesive with my brand. Please refer my brand board. Business name color will be metallic bronzy color. Im thinking grey background or white background. Thanks

Target Market(s)

25-35. Gender neutral. People who are in Entertainment business industry.
This is High-end Eyelash extension salon in Beverly Hills

Industry/Entity Type

Beauty Salon

Contact Information for Business Card

Business name: Lashvera
Name of person: will provide later
Address 4720 N.Alder Crest Ave Larkspur Heights , CA 90299
Phone: will provide later (Text only)
Web: www.lashverastudio.example
Snapgrid icon, Circlebook icon
follow us for seasonal campaign and news @lashverastudiolounge

Requirements
Must have
• Beautiful, elegant, clean and simple look but very attractive and modern
Should not have
• We don't like too clutter, too busy designs.

```html
<!DOCTYPE html>
<html lang="en">
<head>
<meta charset="utf-8">
<title>Lashvera Business Card</title>
<link rel="stylesheet" href="https://fonts.googleapis.com/css2?family=Open+Sans:wght@300;400;700&family=Arimo:wght@700&display=swap">
<style>
  :root {
    --backdrop: #2b2b2c;
    --card: #1b1c1e;
    --pattern: #232427;
    --bronze: #a87b55;
    --rule: #55565a;
    --text: #f2f2f2;
  }
  * { margin: 0; padding: 0; box-sizing: border-box; }
  html, body { width: 1200px; height: 1108px; overflow: hidden; }
  body {
    background: var(--backdrop);
    font-family: "Open Sans", Arial, sans-serif;
    color: var(--text);
    position: relative;
  }
  .card {
    position: absolute;
    top: 204px;
    width: 440px;
    height: 700px;
    background: var(--card);
    border-radius: 28px;
    overflow: hidden;
  }
  .card-front { left: 120px; }
  .card-back { left: 640px; }

  .brand-name {
    position: absolute;
    top: 170px;
    left: 0; right: 0;
    text-align: center;
    font-family: "Open Sans", Arial, sans-serif;
    font-weight: 300;
    font-size: 76px;
    letter-spacing: 1px;
    color: var(--bronze);
  }
  .contact {
    position: absolute;
    top: 428px;
    left: 0; right: 0;
    text-align: center;
  }
  .person-name {
    font-family: "Arimo", Arial, sans-serif;
    font-weight: 700;
    font-size: 25px;
    letter-spacing: 0.5px;
    color: var(--bronze);
    text-transform: uppercase;
  }
  .rule {
    width: 200px;
    height: 1px;
    background: var(--rule);
    margin: 16px auto;
  }
  .address, .reach {
    font-size: 19px;
    line-height: 1.35;
  }

  .pattern-field {
    position: absolute;
    top: 0; left: 0; right: 0;
    height: 470px;
    background: linear-gradient(180deg, var(--pattern), var(--card));
  }
  .follow {
    position: absolute;
    top: 500px;
    left: 40px; right: 40px;
    text-align: center;
  }
  .social-row {
    display: flex;
    align-items: center;
    gap: 12px;
  }
  .social-row .line {
    flex: 1;
    height: 1px;
    background: var(--bronze);
  }
  .social {
    display: flex;
    align-items: center;
    gap: 6px;
    font-size: 14px;
    font-weight: 700;
  }
  .social .dot {
    width: 12px; height: 12px;
    border-radius: 50%;
    background: var(--text);
  }
  .follow-text {
    margin-top: 16px;
    font-size: 19px;
    line-height: 1.4;
  }
  .follow-text strong { font-weight: 700; }
</style>
</head>
<body>
  <section class="card card-front">
    <div class="brand-name">Lashvera</div>
    <div class="contact">
      <div class="person-name">Daniel Reyes</div>
      <div class="rule"></div>
      <div class="address">4720 N.Alder Crest Ave<br>Larkspur Heights , CA 90299</div>
      <div class="rule"></div>
      <div class="reach">044-555 010 234<br>www.lashverastudio.example</div>
    </div>
  </section>

  <section class="card card-back">
    <div class="pattern-field" role="img" aria-label="Faint repeating brand name pattern"></div>
    <div class="follow">
      <div class="social-row">
        <span class="line"></span>
        <span class="social"><span class="dot"></span>Circlebook</span>
        <span class="social"><span class="dot"></span>Snapgrid</span>
        <span class="line"></span>
      </div>
      <p class="follow-text">Follow us for seasonal campaign<br>and news <strong>@lashverastudiolounge</strong></p>
    </div>
  </section>
</body>
</html>
```